Varelko App for Smart Devices IoT WiFi Electronic

Varelko is a siren manufacturer. This application is used for the company's products that have a Wi-Fi connection and an internet connection, which can be configured and activated remotely through this application. In addition, this application is used to activate the siren at specific times for the start and end of shifts in companies and schools. Users will be siren installers and IT or HR managers.
In addition to activating motorized sirens timers, some siren models have speakers and allow you to play TTS (text to speech) audio, audio recorded by the user on the phone and upload audio (mp3) with playlist programming with start and end times.
Application screens: home with dashboard (one dashboard for each category). Device categories: timers, speakers, motorized siren. Screen for requesting evaluation in the Play Store. Screen for registering the user profile. Screen for registering devices according to their category (timers, speakers, motorized siren). Screen for registering device groups. Screen for pairing the device on the client's Wi-Fi network. Screen for registering activation times. Screen for uploading MP3 audios. Screen for registering playlists with audio selection, start and end times. Screen for recording audio for later sending to the speakers. Screen for converting text to speech and sending to the speakers. It is important to have a time picker with the day of the week to program the activation times and playlist.

Target Market(s)

Schools, Companies and Stores.

Industry/Entity Type

IoT

Font styles to use
Sans Serif
Other font styles liked:
• roboto

Colors
FFC000
F8CF3A
FAE287
FDF2CF
FEFAEE

Requirements
Must have
• time picker with weekdays for timer programming feature.
Nice to have
• app review request screen on play store

```html
<!DOCTYPE html>
<html lang="en">
<head>
<meta charset="utf-8">
<title>Varelko – Signup</title>
<link rel="stylesheet" href="https://fonts.googleapis.com/css2?family=Poppins:ital,wght@0,300;0,400;0,500;0,600;1,800&display=swap">
<style>
  :root {
    --amber: #f7bd00;
    --amber-deep: #f0b000;
    --white: #ffffff;
    --ghost: #efefef;
    --ink: #4a5568;
    --muted: #a3a8b1;
    --line: #e4e6ea;
    --bar: #4b5767;
    --eye: #a9b1bd;
  }
  * { box-sizing: border-box; margin: 0; padding: 0; }
  html, body { width: 677px; height: 1200px; overflow: hidden; background: var(--white); }
  body { font-family: "Poppins", sans-serif; color: var(--ink); }

  .screen { position: relative; width: 677px; height: 1200px; overflow: hidden; background: var(--white); }

  .hero-blob { position: absolute; left: 0; top: 0; }

  .status-bar {
    position: absolute; top: 22px; left: 0; right: 0; height: 30px;
    display: flex; justify-content: space-between; align-items: center;
    padding: 0 34px 0 54px; font-weight: 600; font-size: 24px; color: var(--ink);
  }
  .status-icons { display: flex; gap: 9px; align-items: center; }

  .tab-title {
    position: absolute; top: 178px; font-style: italic; font-weight: 800;
    font-size: 122px; line-height: 1; letter-spacing: -2px; white-space: nowrap;
  }
  .tab-title--active { left: -4px; color: var(--white); }
  .tab-title--idle { left: 520px; color: var(--ghost); }

  .signup-card {
    position: absolute; left: 34px; top: 400px; width: 607px; height: 575px;
    background: var(--white); border-radius: 46px;
    box-shadow: 0 40px 90px rgba(0,0,0,0.10), 0 6px 24px rgba(0,0,0,0.04);
    padding: 60px 52px 0;
    display: flex; flex-direction: column; gap: 20px;
  }
  .field {
    height: 78px; border: 2px solid var(--line); border-radius: 39px;
    display: flex; align-items: center; justify-content: space-between;
    padding: 0 34px 0 40px;
  }
  .field-value { font-weight: 500; font-size: 20px; color: var(--ink); }
  .field-value--secret { font-size: 26px; letter-spacing: 4px; padding-top: 10px; }
  .field-label { font-weight: 300; font-size: 16px; color: var(--muted); display: flex; align-items: center; gap: 10px; }

  .submit-button {
    position: absolute; left: 294px; top: 931px; width: 88px; height: 88px;
    border-radius: 50%; background: var(--amber);
    display: flex; align-items: center; justify-content: center;
  }

  .social-bar {
    position: absolute; left: 0; right: 0; bottom: 0; height: 72px; background: var(--bar);
    display: flex; align-items: center; justify-content: center; gap: 12px;
    color: var(--white); font-weight: 500; font-size: 21px; letter-spacing: 0.5px;
  }
  .social-mark { width: 18px; height: 18px; background: var(--white); border-radius: 3px; }
</style>
</head>
<body>
<main class="screen">
  <svg class="hero-blob" width="677" height="700" viewBox="0 0 677 700" aria-hidden="true">
    <defs>
      <linearGradient id="blobFill" x1="0" y1="0" x2="0" y2="1">
        <stop offset="0" stop-color="#f8c000"/>
        <stop offset="1" stop-color="#f0b000"/>
      </linearGradient>
    </defs>
    <circle cx="215" cy="180" r="420" fill="url(#blobFill)" clip-path="none"/>
  </svg>
  <svg class="hero-blob" width="677" height="700" viewBox="0 0 677 700" aria-hidden="true">
    <rect x="0" y="0" width="677" height="700" fill="#ffffff" mask="url(#blobCut)"/>
    <mask id="blobCut">
      <rect width="677" height="700" fill="#fff"/>
      <ellipse cx="150" cy="200" rx="490" ry="470" fill="#000" transform="rotate(-8 150 200)"/>
    </mask>
  </svg>

  <div class="status-bar">
    <span>9:41</span>
    <span class="status-icons">
      <svg width="28" height="18" viewBox="0 0 28 18" aria-hidden="true"><g fill="#4a5568"><rect x="0" y="11" width="5" height="7" rx="1"/><rect x="7" y="8" width="5" height="10" rx="1"/><rect x="14" y="4" width="5" height="14" rx="1"/><rect x="21" y="0" width="5" height="18" rx="1"/></g></svg>
      <svg width="24" height="18" viewBox="0 0 24 18" aria-hidden="true"><g fill="none" stroke="#4a5568" stroke-width="3" stroke-linecap="round"><path d="M2 6.5a14 14 0 0 1 20 0"/><path d="M6 10.5a8 8 0 0 1 12 0"/></g><circle cx="12" cy="15" r="2.4" fill="#4a5568"/></svg>
      <svg width="38" height="18" viewBox="0 0 38 18" aria-hidden="true"><rect x="1" y="1" width="32" height="16" rx="4" fill="none" stroke="#4a5568" stroke-width="2"/><rect x="4" y="4" width="26" height="10" rx="2" fill="#4a5568"/><rect x="35" y="6" width="2.5" height="6" rx="1" fill="#4a5568"/></svg>
    </span>
  </div>

  <h1 class="tab-title tab-title--active">Signup</h1>
  <span class="tab-title tab-title--idle">Log</span>

  <form class="signup-card">
    <div class="field"><span class="field-value">Diponto</span><span class="field-label">First Name</span></div>
    <div class="field"><span class="field-value">Varelko</span><span class="field-label">Last Name</span></div>
    <div class="field"><span class="field-value">Diponto@mailnest.com</span><span class="field-label">Email</span></div>
    <div class="field"><span class="field-value field-value--secret">*********</span><span class="field-label">Password
      <svg width="22" height="14" viewBox="0 0 22 14" aria-hidden="true"><path d="M1 7c3-5 7-6 10-6s7 1 10 6c-3 5-7 6-10 6S4 12 1 7z" fill="#a9b1bd"/><circle cx="11" cy="7" r="3" fill="#fff"/><circle cx="11" cy="7" r="1.6" fill="#a9b1bd"/></svg></span></div>
    <div class="field"><span class="field-value field-value--secret">*********</span><span class="field-label">Confirm Password
      <svg width="22" height="14" viewBox="0 0 22 14" aria-hidden="true"><path d="M1 7c3-5 7-6 10-6s7 1 10 6c-3 5-7 6-10 6S4 12 1 7z" fill="#a9b1bd"/><circle cx="11" cy="7" r="3" fill="#fff"/><circle cx="11" cy="7" r="1.6" fill="#a9b1bd"/></svg></span></div>
  </form>

  <div class="submit-button" aria-label="Continue">
    <svg width="34" height="24" viewBox="0 0 34 24" aria-hidden="true"><g fill="none" stroke="#fff" stroke-width="2.6" stroke-linecap="round" stroke-linejoin="round"><path d="M3 12h27"/><path d="M20 3l10 9-10 9"/></g></svg>
  </div>

  <footer class="social-bar"><span class="social-mark"></span><span>LINKORA</span></footer>
</main>
</body>
</html>
```